Bright Nook Home Page (A Home Wellness e-commerce site & blog)

We need a dynamic home page created for a home wellness brand. Must be visually appealing and extremely mobile-friendly. Logos and a Navmap have been provided but that is just a guideline, PLEASE USE YOUR CREATIVITY.

Target Market(s)

1st target demo: females 24-48, 2nd target demo: all 24-48

Number of Pages Required

1 page

```html
<!DOCTYPE html>
<html lang="en">
<head>
<meta charset="utf-8">
<title>Bright Nook — Home Wellness</title>
<link href="https://fonts.googleapis.com/css2?family=Montserrat:wght@400;600;700&family=Roboto:wght@400;500;700&display=swap" rel="stylesheet">
<style>
:root{
  --purple:#552f94;
  --purple-dark:#4a2885;
  --teal:#32bfca;
  --ink:#111111;
  --text:#555555;
  --muted:#6b6b6b;
  --white:#ffffff;
  --footer:#0b0b0b;
  --line:#e6e6e6;
}
*{box-sizing:border-box;margin:0;padding:0}
html,body{width:1200px;height:4032px;overflow:hidden;background:var(--white)}
body{position:relative;font-family:'Roboto',Arial,sans-serif;color:var(--text)}
.abs{position:absolute}
.heading{font-family:'Montserrat',Arial,sans-serif;color:var(--ink)}
.heading b{font-weight:700}
.heading span{font-weight:400}

/* top bar */
.promo-bar{left:0;top:0;width:1200px;height:45px;background:var(--purple);color:var(--white);font-size:13px;font-weight:700;display:flex;align-items:center;justify-content:center;letter-spacing:.2px}

/* header */
.site-header{left:0;top:45px;width:1200px;height:66px;background:var(--white);border-bottom:1px solid var(--line)}
.brand{left:120px;top:14px;font-family:'Montserrat',Arial,sans-serif;font-weight:600;font-size:31px;color:var(--purple);letter-spacing:-.5px}
.main-nav{left:391px;top:24px;display:flex;gap:22px;font-size:14px;font-weight:500;color:var(--ink)}
.main-nav .active{color:var(--teal)}
.socials{display:flex;gap:6px}
.socials i{width:34px;height:34px;border:1.5px solid var(--teal);border-radius:50%;display:block}
.header-socials{left:875px;top:16px}
.cart{left:1060px;top:20px}

/* hero */
.hero{left:0;top:111px;width:1200px;height:559px;background:linear-gradient(100deg,#e4e4e7 0%,#e2e2e5 55%,#cfd6cc 72%,#8fae85 88%,#6f9669 100%)}
.hero-title{left:108px;top:262px;font-size:80px;line-height:1}
.hero-text{left:111px;top:374px;width:600px;font-size:15.5px;line-height:25px;color:var(--text)}
.btn{display:inline-flex;align-items:center;justify-content:center;gap:12px;background:var(--purple);color:var(--white);font-size:14px;font-weight:700;border-radius:2px}
.hero-btn{left:111px;top:443px;width:142px;height:50px}

/* sale band */
.sale-band{left:0;top:670px;width:1200px;height:164px;background:var(--teal);color:var(--white);font-family:'Montserrat',Arial,sans-serif;font-weight:700;font-size:40px;line-height:46px;text-align:center;display:flex;align-items:center;justify-content:center}

/* section heads */
.section-title{left:0;width:1200px;text-align:center}
.section-sub{left:0;width:1200px;text-align:center;font-size:15px;color:var(--muted)}

/* featured grid */
.tile{border:3px solid var(--white);box-shadow:0 0 0 1px #e2e2e2}

/* about */
.about{left:0;top:1893px;width:1200px;height:480px;background:radial-gradient(ellipse at 50% 50%,#f2f0ee 0%,#ebe8e5 60%,#d9ddd3 100%)}
.about-text{left:230px;top:2068px;width:740px;text-align:center;font-size:16px;line-height:34.5px;color:var(--text)}
.about-btn{left:516px;top:2231px;width:168px;height:50px}

/* pay later band */
.pay-band{left:0;top:2373px;width:1200px;height:208px;background:var(--purple)}
.pay-text{left:160px;top:2419px;font-family:'Montserrat',Arial,sans-serif;font-weight:700;font-size:47px;line-height:52px;color:var(--white)}
.pay-brand{left:837px;top:2450px;display:flex;align-items:center;gap:14px;font-family:'Montserrat',Arial,sans-serif;font-weight:700;font-size:47px;color:var(--white)}
.pay-brand i{width:50px;height:50px;border-radius:50%;background:var(--white);display:block}

/* blog */
.post-img{border:3px solid var(--white);box-shadow:0 0 0 1px #e2e2e2;height:211px;width:316px}
.post-title{font-size:13.5px;font-weight:700;color:var(--ink);width:316px}
.post-text{font-size:13.5px;line-height:21px;color:var(--muted);width:316px}
.learn{font-size:12.5px;font-weight:700;color:var(--teal);text-decoration:underline;display:flex;align-items:center;gap:8px}

/* chat */
.chat-title{left:130px;top:3298px;width:460px;text-align:center;font-size:45px;font-weight:700;line-height:46px}
.chat-text{left:130px;top:3408px;width:460px;text-align:center;font-size:15.5px;line-height:26px;color:var(--muted)}
.chat-btn{left:278px;top:3479px;width:167px;height:50px}

/* footer */
.site-footer{left:0;top:3651px;width:1200px;height:381px;background:var(--footer);color:var(--white)}
.footer-brand{left:111px;top:3722px;font-family:'Montserrat',Arial,sans-serif;font-weight:600;font-size:36px;color:var(--white);letter-spacing:-.5px}
.footer-socials{left:111px;top:3789px}
.foot-head{font-size:14px;font-weight:700;color:var(--white)}
.foot-list{list-style:none;font-size:13.5px;line-height:30.3px;color:var(--white)}
.foot-list li::before{content:"»";margin-right:16px;font-weight:700}
.news-text{left:796px;top:3754px;width:290px;font-size:13.5px;line-height:25px}
.news-input{left:798px;top:3822px;width:184px;height:40px;background:var(--white);color:#888;font-size:13px;display:flex;align-items:center;padding-left:14px}
.news-btn{left:985px;top:3822px;width:101px;height:40px;background:var(--teal);color:var(--white);font-size:13px;font-weight:700;display:flex;align-items:center;justify-content:center}
.foot-rule{left:111px;top:3958px;width:975px;height:1px;background:#3a3a3a}
.copyright{left:0;top:3982px;width:1200px;text-align:center;font-size:13.5px}
.chat-fab{left:1051px;top:3633px;width:36px;height:36px;border-radius:50%;background:var(--teal);display:flex;align-items:center;justify-content:center}
</style>
</head>
<body>

<div class="abs promo-bar">"FREE SHIPPING ON ALL ORDERS $50 AND OVER!"</div>

<header class="abs site-header">
  <div class="abs brand">Bright Nook</div>
  <nav class="abs main-nav">
    <span class="active">Home</span><span>About Us</span><span>Our Products</span><span>Latest Blog</span><span>Contact Us</span>
  </nav>
  <div class="abs socials header-socials"><i></i><i></i><i></i><i></i></div>
  <svg class="abs cart" width="22" height="24" viewBox="0 0 22 24"><path d="M7 8V6a4 4 0 0 1 8 0v2" fill="none" stroke="#552f94" stroke-width="2"/><rect x="2" y="8" width="18" height="15" rx="1" fill="#552f94"/></svg>
</header>

<section class="abs hero" role="img" aria-label="Flat lay of bath salts, green clay jar and fresh eucalyptus leaves on a pale grey surface"></section>
<h1 class="abs heading hero-title"><b>Bright</b> <span>Nook</span></h1>
<p class="abs hero-text">Lorem ipsum dolor sit amet, consectetur adipiscing elit, sed do eiusmod tempor incididunt ut labore et dolore magna aliqua.</p>
<a class="abs btn hero-btn">SHOP NOW
  <svg width="14" height="12" viewBox="0 0 14 12"><path d="M0 1h3l2 7h7l2-6H4" fill="none" stroke="#fff" stroke-width="1.8"/><circle cx="6" cy="10.5" r="1.3" fill="#fff"/><circle cx="11" cy="10.5" r="1.3" fill="#fff"/></svg>
</a>

<div class="abs sale-band">50% off sale going on now! Because saving<br>money also makes us happy</div>

<h2 class="abs heading section-title" style="top:944px;font-size:34px;font-weight:700">Featured Product</h2>
<p class="abs section-sub" style="top:1009px">"The key to total bliss is nurturing the mind, body, and soul"</p>

<div class="abs tile" style="left:111px;top:1073px;width:316px;height:199px;background:linear-gradient(135deg,#f4f3f1,#e3ddd2 60%,#c9b79a)" role="img" aria-label="Spa stones, candles, rolled towel and oil bottle"></div>
<div class="abs tile" style="left:440px;top:1073px;width:316px;height:199px;background:linear-gradient(135deg,#eeeae4,#c8a27a 55%,#6b4a2c)" role="img" aria-label="Amber pump bottles with towels, brush and green leaves"></div>
<div class="abs tile" style="left:111px;top:1286px;width:316px;height:197px;background:linear-gradient(90deg,#e8e4df,#d9c3a6 55%,#7a4d2f)" role="img" aria-label="Cotton swabs in a cup beside amber dropper bottles on a wooden shelf"></div>
<div class="abs tile" style="left:440px;top:1286px;width:316px;height:197px;background:linear-gradient(135deg,#dfe3d8,#b6c8a8 50%,#5d7a4a)" role="img" aria-label="Flat lay of skincare jars and bottles among fern leaves"></div>
<div class="abs tile" style="left:111px;top:1494px;width:316px;height:200px;background:linear-gradient(135deg,#e4e7ea,#e8e8e6 60%,#d7cab5)" role="img" aria-label="Cotton pads, cream in a wooden bowl and eucalyptus sprig"></div>
<div class="abs tile" style="left:440px;top:1494px;width:316px;height:200px;background:linear-gradient(180deg,#f1f1f1,#e7e7e5 65%,#c9ae8c)" role="img" aria-label="Folded white towels and a small plant on a wooden bench"></div>
<div class="abs tile" style="left:765px;top:1073px;width:318px;height:621px;background:linear-gradient(180deg,#f1ebe6,#e8d3c4 50%,#f0e6df)" role="img" aria-label="Portrait of a woman with glowing skin touching her face"></div>

<section class="abs about" role="img" aria-label="Creams, serum bottle and eucalyptus branches on a soft white background"></section>
<h2 class="abs heading section-title" style="top:2002px;font-size:44px"><b>About</b> <span>Us</span></h2>
<p class="abs about-text">They say that home is where the heart is. But home is also where your mind and body reside. At Bright Nook we believe that home should be your place of Zen. A respite from the crazy world outside those walls. It is where you recharge your soul so you can approach each day with the focus and energy necessary to conquer the world.</p>
<a class="abs btn about-btn">TELL ME MORE
  <svg width="14" height="14" viewBox="0 0 14 14"><circle cx="7" cy="7" r="7" fill="#fff"/><path d="M5.5 4l3 3-3 3" fill="none" stroke="#552f94" stroke-width="1.8"/></svg>
</a>

<section class="abs pay-band"></section>
<p class="abs pay-text">Don’t sweat it. You can<br>pay later.</p>
<div class="abs pay-brand"><i></i>Tallypay</div>

<h2 class="abs heading section-title" style="top:2680px;font-size:44px"><b>The Bright</b> <span>Blog</span></h2>
<p class="abs section-sub" style="top:2756px">Food for the mind, tips for the body and exercises for the soul</p>

<article class="abs" style="left:111px;top:2816px">
  <div class="post-img" style="background:linear-gradient(135deg,#c9b3a2,#ece8e4 60%,#dcd9d4)" role="img" aria-label="Woman relaxing with a warm cup of tea"></div>
  <h3 class="post-title" style="margin:34px 0 0 6px">LOREM IPSUM DOLOR SIT AMET, CONS</h3>
  <p class="post-text" style="margin:10px 0 0 6px">Sed ut perspiciatis unde omnis iste natus error sit voluptatem accusantium doloremque</p>
  <a class="learn" style="margin:10px 0 0 8px">LEARN MORE <svg width="11" height="11" viewBox="0 0 14 14"><circle cx="7" cy="7" r="7" fill="#32bfca"/><path d="M5.5 4l3 3-3 3" fill="none" stroke="#fff" stroke-width="2"/></svg></a>
</article>
<article class="abs" style="left:441px;top:2816px">
  <div class="post-img" style="background:linear-gradient(135deg,#5d6b78,#b59272 50%,#d8c2a4)" role="img" aria-label="Woman doing a squat with dumbbells at home"></div>
  <h3 class="post-title" style="margin:34px 0 0 6px">LOREM IPSUM DOLOR SIT AMET, CONS</h3>
  <p class="post-text" style="margin:10px 0 0 6px">Sed ut perspiciatis unde omnis iste natus error sit voluptatem accusantium doloremque</p>
  <a class="learn" style="margin:10px 0 0 8px">LEARN MORE <svg width="11" height="11" viewBox="0 0 14 14"><circle cx="7" cy="7" r="7" fill="#32bfca"/><path d="M5.5 4l3 3-3 3" fill="none" stroke="#fff" stroke-width="2"/></svg></a>
</article>
<article class="abs" style="left:771px;top:2816px">
  <div class="post-img" style="background:linear-gradient(135deg,#dfe4e6,#c4c9cb 50%,#8a7a68)" role="img" aria-label="Man doing push-ups on a living room rug"></div>
  <h3 class="post-title" style="margin:34px 0 0 6px">LOREM IPSUM DOLOR SIT AMET, CONS</h3>
  <p class="post-text" style="margin:10px 0 0 6px">Sed ut perspiciatis unde omnis iste natus error sit voluptatem accusantium doloremque</p>
  <a class="learn" style="margin:10px 0 0 8px">LEARN MORE <svg width="11" height="11" viewBox="0 0 14 14"><circle cx="7" cy="7" r="7" fill="#32bfca"/><path d="M5.5 4l3 3-3 3" fill="none" stroke="#fff" stroke-width="2"/></svg></a>
</article>

<h2 class="abs heading chat-title">Got questions?<br>Let’s chat!</h2>
<p class="abs chat-text">Sed ut perspiciatis unde omnis iste natus error sit voluptatem accusantium doloremque laudantium, totam</p>
<a class="abs btn chat-btn">CHAT WITH US
  <svg width="16" height="13" viewBox="0 0 16 13"><ellipse cx="7" cy="5.5" rx="6" ry="4.5" fill="none" stroke="#fff" stroke-width="1.6"/><path d="M3 9l-1 3 4-2" fill="#fff"/></svg>
</a>
<div class="abs" style="left:610px;top:3270px;width:454px;height:266px;background:radial-gradient(ellipse at 50% 55%,#e8c9a0 0%,#f3e6d6 45%,#ffffff 72%)" role="img" aria-label="Wooden tray with soaps, flower, spa stones and bath salts"></div>

<footer class="abs site-footer"></footer>
<div class="abs chat-fab"><svg width="18" height="15" viewBox="0 0 16 13"><ellipse cx="7" cy="5.5" rx="6" ry="4.5" fill="none" stroke="#fff" stroke-width="1.6"/><path d="M3 9l-1 3 4-2" fill="#fff"/></svg></div>
<div class="abs footer-brand">Bright Nook</div>
<div class="abs socials footer-socials"><i></i><i></i><i></i><i></i></div>

<h4 class="abs foot-head" style="left:407px;top:3719px">NAVIGATE</h4>
<ul class="abs foot-list" style="left:407px;top:3748px">
  <li>Home</li><li>About Us</li><li>Our Products</li><li>Latest Blog</li><li>Contact Us</li>
</ul>
<ul class="abs foot-list" style="left:571px;top:3748px">
  <li>Terms &amp; Conditions</li><li>Privacy Policy</li><li>Help Service</li><li>FAQ</li><li>Portfolio</li>
</ul>

<h4 class="abs foot-head" style="left:796px;top:3719px">SIGN UP FOR OUR NEWSLETTER</h4>
<p class="abs news-text">Lorem ipsum dolor sit ame consectetur adipiscing elit, sed do eiusmod</p>
<div class="abs news-input">Email Address</div>
<div class="abs news-btn">SUBMIT NOW</div>

<div class="abs foot-rule"></div>
<p class="abs copyright">© 2021 Bright Nook. All Rights Reserved</p>

</body>
</html>
```